International Petrochemical business needs a web design for Clearway Desk system

We need a web design for a "Clearway Desk" system for an international petrochemical company. The web site is used internally within the company. It is hosted by an internal department which provides government permit request service for other departments.

We would like to see designs of two pages using color light blue. (home page, internal page as attached).
Home Page:
1. Header has a background image and small animation. Header on home page can be taller than the header of the internal page.
2. Layout as attached.

Internal Page:
1. Header can use the same background image as the home page and can be shorter to utilize the page for content.
2. The blue icon behind every captions represent an icon. When user move mouse over this icon, it displays the caption in Thai language as a tooltip. This icon needs to be redesign.

The final design should communicate the followings:
- Excellent service provided system in terms of time and accurary
- Rapid growth of business via building petrochemical refinery plant
Updates

For Internal Page, the blue circle behind every captions represent an icon. When mouse over this icon, a tool tip showing the caption in Thai language is shown. Please also design this icon..

There are more feedbacks from customer as followed:

1. Banner should consists of 
    1.1 "Approved" stamp on paper
    1.2 An image of Garuda. It is used on every government documents in Thailand
    1.3 Image of petrochemical plant
2. Each menu item (Home, Permit, Search, etc) should have different colors. Drop down menu will use the same color as its parent menu item.
3. Overall tone of the web page should be light blue with background of the body the web page in white
4. "New Request" button should use green color with icon on it
5. Table header of each box in the body of the page should use dark blue background with text in white

Please kindly submit your revisions.
Thank you.

Industry/Entity Type

Business

Requirements
Must have
• 1. Design for 1024x768 screen resolution
2. Use light blue theme
3. Background of header where the company logo is must have white background

```html
<!DOCTYPE html>
<html lang="en">
<head>
<meta charset="utf-8">
<title>Clearway Desk</title>
<link rel="stylesheet" href="https://fonts.googleapis.com/css2?family=Open+Sans:wght@400;600;700&family=Roboto:wght@700;900&family=Sarabun:wght@400&display=swap">
<style>
:root{
  --white:#ffffff;
  --brand:#1a73c9;
  --title-top:#3a8fd8;
  --title-bottom:#1b4f95;
  --nav-top:#8fcdf0;
  --nav-bottom:#4fa6dc;
  --menu-bg:#e4edf5;
  --menu-text:#2a3f66;
  --hero-a:#5d6b78;
  --hero-b:#aab6c0;
  --hero-c:#d9e6ef;
  --body-top:#8cc8ee;
  --body-bottom:#1e8ad6;
  --panel-top:#d4ecfb;
  --panel-bottom:#b4dbf5;
  --panel-line:#6fb0e4;
  --head-top:#4aa6ec;
  --head-bottom:#1561b8;
  --ink:#1c2430;
  --link:#2b63c9;
  --divider:#9cc6e6;
  --pager-tab:#5fb0ec;
  --pager-dot:#1b3b78;
  --footer-top:#0e3a6d;
  --footer-bottom:#0a2a55;
  --red:#e0252a;
  --amber:#f2c21b;
}
*{box-sizing:border-box;margin:0;padding:0}
html,body{width:1104px;height:1200px;overflow:hidden}
body{position:relative;background:var(--white);font-family:"Open Sans",Arial,sans-serif;color:var(--ink)}

.site-header{position:absolute;left:0;top:0;width:1104px;height:86px;background:var(--white)}
.brand{position:absolute;left:78px;top:26px;display:flex;align-items:center;gap:8px}
.brand-mark{width:30px;height:30px;border-radius:50%;background:var(--brand)}
.brand-name{font-weight:700;font-size:17px;line-height:18px;color:var(--brand)}
.app-title{position:absolute;left:336px;top:36px;font-family:"Roboto",Arial,sans-serif;font-weight:900;font-size:38px;letter-spacing:1px;
  background:linear-gradient(var(--title-top),var(--title-bottom));-webkit-background-clip:text;background-clip:text;color:transparent}

.main-nav{position:absolute;left:0;top:86px;width:1104px;height:46px;background:linear-gradient(var(--nav-top),var(--nav-bottom))}
.main-nav ul{list-style:none;display:flex;position:absolute;left:99px;top:14px}
.main-nav li{color:var(--white);font-size:14px;text-shadow:0 1px 2px rgba(0,0,0,.35);white-space:nowrap}
.main-nav .sep{margin:0 36px 0 38px}
.submenu{position:absolute;left:177px;top:135px;width:142px;height:89px;background:var(--menu-bg);box-shadow:0 2px 4px rgba(0,0,0,.25);z-index:2;padding-top:6px}
.submenu a{display:block;font-size:12px;color:var(--menu-text);padding:4px 0 8px 11px;text-decoration:none;border-bottom:1px solid #c8d6e4}
.submenu a:last-child{border-bottom:0}

.hero{position:absolute;left:0;top:135px;width:1104px;height:259px;
  background:linear-gradient(100deg,var(--hero-a) 0%,var(--hero-b) 45%,var(--hero-c) 85%,#eef4f8 100%)}

.content{position:absolute;left:0;top:394px;width:1104px;height:710px;background:linear-gradient(var(--body-top),var(--body-bottom))}

.panel{position:absolute;border-radius:14px;background:linear-gradient(var(--panel-top),var(--panel-bottom));border:1px solid var(--panel-line);box-shadow:0 2px 5px rgba(0,40,90,.35);overflow:hidden}
.panel-title{height:42px;background:linear-gradient(var(--head-top),var(--head-bottom));color:var(--white);font-weight:700;font-size:18px;padding:9px 0 0 13px;border-radius:14px 14px 40% 40%/14px 14px 8px 8px;text-shadow:0 1px 2px rgba(0,0,0,.35)}
.grid{position:absolute;top:52px;left:0;right:0;display:grid}
.col{border-left:1px solid var(--divider);padding-left:13px;min-height:100px}
.col:first-child{border-left:0}
.col h3{font-size:16px;font-weight:600;line-height:20px;height:27px}
.col p{font-size:12.5px;line-height:19.4px}
.col a{color:var(--link);font-size:12.5px;line-height:19.4px;display:block}
.thai{font-family:"Sarabun",sans-serif}
.due{display:flex;align-items:center;gap:6px}
.dot{width:14px;height:14px;border-radius:50%;display:inline-block}
.dot.red{background:var(--red)}
.dot.amber{background:var(--amber)}

.pager{position:absolute;bottom:0;left:50%;transform:translateX(-50%);width:132px;height:28px;background:var(--pager-tab);border-radius:12px 12px 0 0;display:flex;align-items:center;justify-content:center;gap:3px;box-shadow:0 -1px 2px rgba(0,40,90,.25)}
.pager span{width:15px;height:15px;border-radius:50%;background:var(--pager-dot);color:var(--white);font-size:9px;font-weight:700;display:flex;align-items:center;justify-content:center}
.pager span.on{background:var(--white);color:var(--pager-dot)}
.pager svg{width:10px;height:12px}

.new-request{position:absolute;left:575px;top:428px;width:490px;height:58px;border-radius:14px;background:linear-gradient(var(--head-top),var(--head-bottom));border:1px solid var(--panel-line);box-shadow:0 2px 5px rgba(0,40,90,.35);color:var(--white);font-family:"Roboto",Arial,sans-serif;font-weight:700;font-size:22px;display:flex;align-items:center;justify-content:center;text-shadow:0 1px 2px rgba(0,0,0,.35)}

.site-footer{position:absolute;left:0;top:1104px;width:1104px;height:96px;background:linear-gradient(var(--footer-top),var(--footer-bottom));color:var(--white);font-size:10px}
.site-footer .copy{position:absolute;left:80px;top:21px}
.site-footer .legal{position:absolute;right:52px;top:21px}
</style>
</head>
<body>

<header class="site-header">
  <div class="brand"><span class="brand-mark"></span><span class="brand-name">Halvern<br>Petrochemical</span></div>
  <div class="app-title">CLEARWAY DESK</div>
</header>

<nav class="main-nav">
  <ul>
    <li>HOME</li><li class="sep">|</li>
    <li>PERMITS</li><li class="sep">|</li>
    <li>SEARCH</li><li class="sep">|</li>
    <li>REPORT</li><li class="sep">|</li>
    <li>ADMIN</li><li class="sep">|</li>
    <li>HELP</li>
  </ul>
</nav>
<div class="submenu">
  <a href="#">Create New Permit</a>
  <a href="#">Transfer Role</a>
  <a href="#">Transfer Res. Person</a>
</div>

<div class="hero" role="img" aria-label="Photo of a petrochemical refinery plant with pipes, stairways and distillation towers"></div>

<main class="content">
  <section class="panel" style="left:63px;top:16px;width:490px;height:204px">
    <div class="panel-title">New Requests</div>
    <div class="grid" style="grid-template-columns:168px 172px 1fr">
      <div class="col"><h3>Request No.</h3><a href="#">56-0003</a><a href="#">56-0004</a></div>
      <div class="col"><h3>Requested Date</h3><p>20/4/2013</p><p>21/4/2013</p></div>
      <div class="col"><h3>Branch</h3><p>GC1</p><p>GC2</p></div>
    </div>
    <div class="pager"><svg viewBox="0 0 10 12"><path d="M7 1 2 6l5 5" stroke="#1b3b78" stroke-width="2" fill="none"/></svg><span class="on">1</span><span>2</span><span>3</span><span>4</span><span>5</span><svg viewBox="0 0 10 12"><path d="M3 1l5 5-5 5" stroke="#1b3b78" stroke-width="2" fill="none"/></svg></div>
  </section>

  <section class="panel" style="left:576px;top:16px;width:490px;height:204px">
    <div class="panel-title">My Working Requests</div>
    <div class="grid" style="grid-template-columns:168px 168px 1fr">
      <div class="col"><h3>Request No.</h3><a href="#">56-0003</a><a href="#">56-0004</a><a href="#">56-0005</a><a href="#">56-0006</a></div>
      <div class="col"><h3>Requested Date</h3><p>20/4/2013</p><p>21/4/2013</p><p>20/4/2013</p><p>21/4/2013</p></div>
      <div class="col"><h3>Status</h3><p>Waiting for process</p><p>In progress</p><p>Incomplete document</p><p>Cancel requested</p></div>
    </div>
    <div class="pager"><svg viewBox="0 0 10 12"><path d="M7 1 2 6l5 5" stroke="#1b3b78" stroke-width="2" fill="none"/></svg><span class="on">1</span><span>2</span><span>3</span><span>4</span><span>5</span><svg viewBox="0 0 10 12"><path d="M3 1l5 5-5 5" stroke="#1b3b78" stroke-width="2" fill="none"/></svg></div>
  </section>

  <section class="panel" style="left:63px;top:238px;width:1003px;height:170px">
    <div class="panel-title">Expiring Permits</div>
    <div class="grid" style="grid-template-columns:166px 171px 177px 169px 167px 1fr">
      <div class="col"><h3>Permit No</h3><a href="#">AB56001</a><a href="#">BIO5502</a></div>
      <div class="col"><h3>Expire Date</h3><p>25/3/2013</p><p>24/3/2013</p></div>
      <div class="col"><h3>Permit Name</h3><p>Permit Name ###10</p><p>Permit Name ###20</p></div>
      <div class="col"><h3>Branch</h3><p>GC1</p><p>GC2</p></div>
      <div class="col" style="min-height:80px"><h3 style="height:auto">Required Time<br>(Day)</h3><p style="margin-top:-1px">30</p><p>60</p></div>
      <div class="col"><h3>Due Date</h3><p class="due"><span class="dot red"></span>-40</p><p class="due"><span class="dot amber"></span>-15</p></div>
    </div>
    <div class="pager"><svg viewBox="0 0 10 12"><path d="M7 1 2 6l5 5" stroke="#1b3b78" stroke-width="2" fill="none"/></svg><span class="on">1</span><span>2</span><span>3</span><span>4</span><span>5</span><svg viewBox="0 0 10 12"><path d="M3 1l5 5-5 5" stroke="#1b3b78" stroke-width="2" fill="none"/></svg></div>
  </section>

  <section class="panel" style="left:63px;top:428px;width:490px;height:249px">
    <div class="panel-title">My In Progress Requests</div>
    <div class="grid" style="grid-template-columns:168px 172px 1fr">
      <div class="col" style="min-height:170px"><h3>Request No.</h3><a href="#">56-0001</a><a href="#">56-0002</a></div>
      <div class="col" style="min-height:170px"><h3>Requested Date</h3><p>20/4/2013</p><p>21/4/2013</p></div>
      <div class="col" style="min-height:170px"><h3>Status</h3><p class="thai">ระหว่างดำเนินการ</p><p class="thai">รอดำเนินการ</p></div>
    </div>
    <div class="pager"><svg viewBox="0 0 10 12"><path d="M7 1 2 6l5 5" stroke="#1b3b78" stroke-width="2" fill="none"/></svg><span class="on">1</span><span>2</span><span>3</span><span>4</span><span>5</span><svg viewBox="0 0 10 12"><path d="M3 1l5 5-5 5" stroke="#1b3b78" stroke-width="2" fill="none"/></svg></div>
  </section>

  <div class="new-request">NEW REQUEST</div>

  <section class="panel" style="left:576px;top:500px;width:490px;height:177px">
    <div class="panel-title">Recent Completed Requests</div>
    <div class="grid" style="grid-template-columns:249px 1fr">
      <div class="col"><h3>Request No.</h3><a href="#">55-0100</a><a href="#">55-0088</a><a href="#">55-0002</a></div>
      <div class="col"><h3>Completed Date</h3><p>25/3/2013</p><p>24/3/2013</p><p>18/1/2013</p></div>
    </div>
    <div class="pager"><svg viewBox="0 0 10 12"><path d="M7 1 2 6l5 5" stroke="#1b3b78" stroke-width="2" fill="none"/></svg><span class="on">1</span><span>2</span><span>3</span><span>4</span><span>5</span><svg viewBox="0 0 10 12"><path d="M3 1l5 5-5 5" stroke="#1b3b78" stroke-width="2" fill="none"/></svg></div>
  </section>
</main>

<footer class="site-footer">
  <p class="copy">Copyright © 2013 HalvernPetrochemical. All rights reserved.</p>
  <p class="legal">Terms and Condition | Privacy</p>
</footer>

</body>
</html>
```